Namecard Designs+Logo for a High End Automobile Company

We need a new business card for our company called Nordel Motorwerk.

www.nordelmotorwerk.example.sg
Our new website will be up in 2.5 months time.

We sell used and brand new continental cars like Valcrest, KTR, Almira, Dunvale and etc. Currently we are operating from 2 offices in Singapore and United Kingdom.

We want a design which is serious. We are open to colours but try to keep it at a maximum of 3 colours.

We prefer something simple and minimal. We are open to 2 sides printing or even 2 sided namecards. Both UK and Singapore company offices address must be in; either side by side, front and back, or even 2 sided cards.

The logo can be a text logo, emblem, abstract, pictorial or combination.

We are printing with Printlyx.com so please kindly follow the printing guideline.

http://uk.printlyx.example/help/faq/templates-and-guidelines.html

Rich and Car Enthusiasts

Printing

• Our 2 offices; UK and Singapore.

Our slogan which is " The Automobile Specialist"
• Not more than 3 colours

```html
<!DOCTYPE html>
<html lang="en">
<head>
<meta charset="utf-8">
<title>Nordel Motorwerk – Business Card</title>
<link rel="stylesheet" href="https://fonts.googleapis.com/css2?family=Crimson+Text:wght@400&family=Noto+Serif:wght@400&display=swap">
<style>
  :root {
    --paper: #ffffff;
    --ink: #1f2326;
    --card-grey: #7b7b7b;
    --tread-grey: #808080;
    --tread-light: #e2e2e2;
    --frame: #8c8c8c;
    --trim: #9a9a9a;
    --light-text: #ffffff;
  }
  * { margin: 0; padding: 0; box-sizing: border-box; }
  html, body {
    width: 790px; height: 1200px; overflow: hidden;
    background: var(--paper);
  }
  .sheet { position: relative; width: 790px; height: 1200px; }
  .trim-area {
    position: absolute; left: 0; width: 786px;
    border: 1px dotted var(--trim);
  }
  .trim-area--front { top: 0; height: 573px; border-top: none; border-left: none; }
  .trim-area--back { top: 632px; height: 568px; border-bottom: none; }

  .card {
    position: absolute; left: 34px; width: 717px; height: 470px;
    border-radius: 0 28px 0 28px;
    overflow: hidden;
  }
  .card--front { top: 42px; background: var(--paper); border: 2px solid var(--frame); }
  .card--back { top: 694px; left: 40px; background: var(--card-grey); }

  .card__art { position: absolute; left: 0; top: 0; }

  .brand {
    position: absolute; text-align: center;
    font-family: "Crimson Text", Georgia, serif; color: var(--ink);
  }
  .brand__name { display: flex; align-items: center; justify-content: center; gap: 10px; line-height: 1; }
  .brand__mark { width: 30px; height: 30px; border-radius: 50%; background: var(--ink); flex: none; }
  .brand__slogan { line-height: 1; }

  .brand--front { left: 247px; top: 330px; width: 300px; }
  .brand--front .brand__name { font-size: 38px; }
  .brand--front .brand__slogan { font-size: 20px; margin-top: 36px; }

  .brand--back {
    left: 93px; top: 0; width: 174px; height: 105px;
    padding-top: 30px; background: var(--tread-grey);
  }
  .brand--back .brand__name { font-size: 17px; gap: 5px; }
  .brand--back .brand__mark { width: 13px; height: 13px; }
  .brand--back .brand__slogan { font-size: 11px; color: var(--tread-light); margin-top: 12px; }

  .office { position: absolute; left: 116px; }
  .office__title {
    font-family: "Crimson Text", Georgia, serif; color: var(--light-text);
    font-size: 24px; line-height: 1; font-weight: 400;
  }
  .office__title small { font-size: 16px; letter-spacing: 0.5px; }
  .office__sub { display: block; font-size: 16px; margin-top: 2px; letter-spacing: 0.5px; }
  .office__address {
    font-family: "Noto Serif", Georgia, serif; font-style: normal;
    color: var(--ink); font-size: 16px; line-height: 20px;
    margin-top: 22px;
  }
  .office--uk { top: 150px; }
  .office--sg { top: 289px; }
  .office--sg .office__address { margin-top: 20px; }
</style>
</head>
<body>
<main class="sheet">
  <div class="trim-area trim-area--front"></div>
  <div class="trim-area trim-area--back"></div>

  <section class="card card--front" aria-label="Card front">
    <svg class="card__art" width="717" height="470" viewBox="0 0 717 470">
      <path role="img" aria-label="Curving tyre track running down to the brand name"
            d="M237 0 L383 0 C432 100 472 200 472 313 L302 313 C302 205 280 100 237 0 Z"
            fill="var(--tread-grey)"/>
    </svg>
    <div class="brand brand--front">
      <div class="brand__name"><span class="brand__mark"></span>Nordel Motorwerk</div>
      <p class="brand__slogan">The Automobile Specialist</p>
    </div>
  </section>

  <section class="card card--back" aria-label="Card back">
    <svg class="card__art" width="717" height="470" viewBox="0 0 717 470">
      <path role="img" aria-label="Tyre tread sweeping across the top left corner"
            d="M0 0 L93 0 L93 107 C60 95 30 88 0 92 Z" fill="var(--tread-light)"/>
      <path role="img" aria-label="Arched tyre tread across the top edge"
            d="M267 0 L717 0 L717 118 C620 70 520 40 430 42 C360 44 300 70 267 100 Z"
            fill="var(--tread-light)"/>
    </svg>
    <div class="brand brand--back">
      <div class="brand__name"><span class="brand__mark"></span>Nordel Motorwerk</div>
      <p class="brand__slogan">The Automobile Specialist</p>
    </div>

    <div class="office office--uk">
      <h2 class="office__title">UK <small>OFFICE</small></h2>
      <address class="office__address">27 Harrow Lane.<br>City, London.</address>
    </div>

    <div class="office office--sg">
      <h2 class="office__title">SINGAPORE<span class="office__sub">OFFICE</span></h2>
      <address class="office__address">8 Crescent Hill<br>Rd Block 3B<br>Singapore 304417</address>
    </div>
  </section>
</main>
</body>
</html>
```